Telecommunications/Power civil contractor needs business card design

Were a new telecommunications/power underground civil contractor that is looking for a new business card design. Our company colours are silver or grey and orange. Feel free to use the white background logo or the black background logo.

Target Market(s)

Local contractors, utility companies, private sector mining/energy companies, developers.

Industry/Entity Type

Telecommunications

Contact Information for Business Card

Each card will need the following info:
Persons name:
Title:
E-mail:
Phone number:
Shop Address:
Mailing Address:

Requirements
Must have
• Each card will need the following info:
• Persons name:
• Title:
• E-mail:
• Phone number:
• Shop Address:
• Mailing Address:

```html
<!DOCTYPE html>
<html lang="en">
<head>
<meta charset="utf-8">
<title>Kestrel Line Civil Inc — Business Card</title>
<link rel="stylesheet" href="https://fonts.googleapis.com/css2?family=Saira:wght@400;600;700&display=swap">
<style>
  :root {
    --stage: #3a3230;
    --card: #111111;
    --card-edge: #1c1c1c;
    --orange: #f26522;
    --silver: #a7a9ac;
    --silver-light: #d4d5d7;
    --text-grey: #b3b3b3;
    --divider: #4a4a4a;
  }
  * { box-sizing: border-box; margin: 0; padding: 0; }
  html, body {
    width: 1200px;
    height: 814px;
    overflow: hidden;
    background: var(--stage);
    font-family: "Saira", "Arial", sans-serif;
  }
  .stage {
    position: relative;
    width: 1200px;
    height: 814px;
    display: flex;
    align-items: center;
    justify-content: center;
    gap: 44px;
  }
  .card {
    width: 540px;
    height: 309px;
    background: var(--card);
    border: 1px solid var(--card-edge);
    box-shadow: 0 14px 30px rgba(0,0,0,0.45);
    position: relative;
  }

  /* Front */
  .card-front {
    display: flex;
    align-items: center;
  }
  .brand-block {
    width: 262px;
    display: flex;
    flex-direction: column;
    align-items: center;
    gap: 14px;
    padding-top: 20px;
  }
  .brand-dot {
    width: 70px;
    height: 70px;
    border-radius: 50%;
    border: 5px solid var(--silver);
  }
  .brand-name {
    color: var(--orange);
    font-weight: 700;
    font-size: 22px;
    line-height: 1.05;
    text-align: center;
    letter-spacing: 0.5px;
  }
  .divider {
    width: 1px;
    height: 210px;
    background: var(--divider);
  }
  .contact-block {
    padding-left: 24px;
    color: var(--text-grey);
    font-size: 14px;
    line-height: 1.5;
  }
  .person-name {
    color: var(--orange);
    font-weight: 600;
    font-size: 19px;
    letter-spacing: 0.5px;
    line-height: 1.2;
  }
  .person-title {
    font-size: 14px;
    margin-bottom: 14px;
  }
  .address { margin-bottom: 6px; }
  .contact-line {
    display: flex;
    align-items: center;
    gap: 10px;
  }
  .contact-line svg { width: 12px; height: 12px; flex: none; }

  /* Back */
  .card-back {
    display: flex;
    flex-direction: column;
    align-items: center;
    justify-content: center;
    gap: 18px;
  }
  .back-ring {
    width: 120px;
    height: 120px;
    border-radius: 50%;
    border: 6px solid var(--silver-light);
  }
  .back-name {
    color: var(--silver-light);
    font-weight: 700;
    font-size: 22px;
    letter-spacing: 0.5px;
  }
</style>
</head>
<body>
<main class="stage">
  <section class="card card-front" aria-label="Business card front">
    <div class="brand-block">
      <span class="brand-dot" aria-hidden="true"></span>
      <p class="brand-name">KESTREL LINE<br>CIVIL INC</p>
    </div>
    <span class="divider" aria-hidden="true"></span>
    <div class="contact-block">
      <p class="person-name">DANA WHITLOW</p>
      <p class="person-title">CEO/FOUNDER</p>
      <p class="address">2140 Birchwood Road<br>Fairbanks, Alaska 99701</p>
      <p class="contact-line">
        <svg viewBox="0 0 12 12" aria-hidden="true"><path fill="var(--orange)" d="M2.5 0.5 L4.5 0.5 L5 3.5 L3.6 4.4 Q4.8 7 7.6 8.4 L8.5 7 L11.5 7.5 L11.5 9.5 Q11.5 11.5 9.5 11.5 Q0.5 10.5 0.5 2.5 Q0.5 0.5 2.5 0.5 Z"/></svg>
        555 201 4476
      </p>
      <p class="contact-line">
        <svg viewBox="0 0 12 12" aria-hidden="true"><rect x="0.5" y="2" width="11" height="8" fill="var(--orange)"/><path d="M0.5 2 L6 6.5 L11.5 2" fill="none" stroke="var(--card)" stroke-width="1"/></svg>
        dana@kestrelcivil.com
      </p>
      <p class="contact-line">
        <svg viewBox="0 0 12 12" aria-hidden="true"><circle cx="6" cy="6" r="5.5" fill="var(--orange)"/><path d="M0.5 6 H11.5 M6 0.5 Q2.5 6 6 11.5 M6 0.5 Q9.5 6 6 11.5" fill="none" stroke="var(--card)" stroke-width="0.8"/></svg>
        www.kestrelcivil.com
      </p>
    </div>
  </section>

  <section class="card card-back" aria-label="Business card back">
    <span class="back-ring" aria-hidden="true"></span>
    <p class="back-name">KESTREL LINE CIVIL INC</p>
  </section>
</main>
</body>
</html>
```